Corvane Holdings , new business card design

investment firm with corporate clients . need double sided business card , vertical and horizontal options ,logo must be clear. prefer pantone colors only and sharp design. website also www.corvane.ae

Khalid Bin Tarrafi
Managing Director
Tel. +971 4 387 2940
Mobile +971 50 518 2403
khalid@corvane.ae
Q-Span Plaza, officw 18-B07, Warqa Gardens, Dubai

Contact Information for Business Card

Khalid Bin Tarrafi
Managing Director

Font styles to use
Serif

Colors

Designer to choose colors to be used in the design.

```html
<!DOCTYPE html>
<html lang="en">
<head>
<meta charset="utf-8">
<title>Corvane Holdings — Business Card</title>
<link rel="stylesheet" href="https://fonts.googleapis.com/css2?family=Roboto:wght@300;400&family=Roboto+Condensed:wght@700&display=swap">
<style>
  :root {
    --backdrop: #dedede;
    --card-white: #f6f6f6;
    --brand-blue: #436d93;
    --ink-dark: #1c1c1c;
    --ink-grey: #4a4a4a;
    --rule-grey: #b9b9b9;
    --paper-white: #ffffff;
  }
  * { margin: 0; padding: 0; box-sizing: border-box; }
  html, body {
    width: 1200px; height: 960px; overflow: hidden;
    background: var(--backdrop);
    font-family: "Roboto", Arial, sans-serif;
  }
  .canvas { position: relative; width: 1200px; height: 960px; }

  .card {
    position: absolute; width: 600px; height: 343px;
  }
  .card--front { left: 314px; top: 113px; background: var(--card-white); }
  .card--back  { left: 311px; top: 472px; background: var(--brand-blue); }

  .wordmark {
    position: absolute; text-align: center; font-weight: 300;
  }
  .wordmark__name {
    display: block; font-size: 40px; letter-spacing: 10px; line-height: 1;
    padding-left: 10px;
  }
  .wordmark__sub {
    display: block; font-size: 13px; letter-spacing: 11.5px; margin-top: 8px;
    padding-left: 11px;
  }
  .card--front .wordmark { left: 46px; top: 145px; width: 244px; color: var(--ink-dark); }
  .card--back .wordmark  { left: 145px; top: 137px; width: 310px; color: var(--paper-white); }
  .card--back .wordmark__name { font-size: 48px; letter-spacing: 14px; padding-left: 14px; }
  .card--back .wordmark__sub  { font-size: 15px; letter-spacing: 15px; padding-left: 15px; }

  .divider {
    position: absolute; left: 318px; top: 87px; width: 1px; height: 173px;
    background: var(--rule-grey);
  }

  .contact { position: absolute; left: 343px; top: 83px; }
  .contact__name {
    font-family: "Roboto Condensed", "Arial Narrow", sans-serif; font-weight: 700;
    font-size: 21px; color: var(--brand-blue); line-height: 24px;
  }
  .contact__role {
    font-size: 15px; color: var(--ink-dark); line-height: 20px; margin-top: 1px;
  }
  .contact__address {
    font-size: 14px; color: var(--ink-grey); line-height: 18px; margin-top: 11px;
    font-style: normal;
  }
  .contact__list { list-style: none; margin-top: 9px; }
  .contact__item {
    display: flex; align-items: center; gap: 7px;
    font-size: 14.5px; color: var(--ink-grey); line-height: 19px;
  }
  .contact__icon { width: 13px; height: 13px; flex: none; fill: var(--brand-blue); }

  .card__web {
    position: absolute; left: 0; width: 100%; top: 290px; text-align: center;
    color: var(--paper-white); font-size: 14px; letter-spacing: 9px; font-weight: 400;
    padding-left: 9px;
  }
</style>
</head>
<body>
<main class="canvas">
  <section class="card card--front" aria-label="Card front">
    <div class="wordmark">
      <span class="wordmark__name">CORVANE</span>
      <span class="wordmark__sub">HOLDINGS</span>
    </div>
    <div class="divider"></div>
    <div class="contact">
      <h1 class="contact__name">KHALID BIN TARRAFI</h1>
      <p class="contact__role">MANAGING DIRECTOR</p>
      <address class="contact__address">Q-Span Plaza, officw 18-B07<br>Warqa Gardens, Dubai</address>
      <ul class="contact__list">
        <li class="contact__item">
          <svg class="contact__icon" viewBox="0 0 16 16" aria-hidden="true"><path d="M3.5 1l2.6 3.2-1.4 1.8c.9 2 2.4 3.5 4.4 4.4l1.8-1.4L14.1 11.6 12.6 14.5C6.6 14 2 9.4 1.5 3.4z"/></svg>
          +971 4 387 2940
        </li>
        <li class="contact__item">
          <svg class="contact__icon" viewBox="0 0 16 16" aria-hidden="true"><path d="M4 0h8a1 1 0 0 1 1 1v14a1 1 0 0 1-1 1H4a1 1 0 0 1-1-1V1a1 1 0 0 1 1-1zm.6 2v10.5h6.8V2zM8 13.3a.9.9 0 1 0 0 1.8.9.9 0 0 0 0-1.8z" fill-rule="evenodd"/></svg>
          +971 50 518 2403
        </li>
        <li class="contact__item">
          <svg class="contact__icon" viewBox="0 0 16 16" aria-hidden="true"><path d="M1 3h14v1.2L8 8.6 1 4.2zm0 2.6l7 4.4 7-4.4V13H1z"/></svg>
          khalid@corvane.ae
        </li>
        <li class="contact__item">
          <svg class="contact__icon" viewBox="0 0 16 16" aria-hidden="true"><circle cx="8" cy="8" r="7"/><path d="M1 8h14M8 1c2.5 2.5 2.5 11.5 0 14M8 1c-2.5 2.5-2.5 11.5 0 14" stroke="#f6f6f6" stroke-width="1" fill="none"/></svg>
          www.corvane.ae
        </li>
      </ul>
    </div>
  </section>

  <section class="card card--back" aria-label="Card back">
    <div class="wordmark">
      <span class="wordmark__name">CORVANE</span>
      <span class="wordmark__sub">HOLDINGS</span>
    </div>
    <p class="card__web">www.corvane.ae</p>
  </section>
</main>
</body>
</html>
```